Packaging and logo design for washcloths

We are a company manufacturing towels and washcloths for babies.We are planning to get into e-commerce business with washcloths for babies made out of 100% Rayon made from Bamboo.We would like to see a logo design that symbolizes the perfection of the nature and a packaging design that gives mothers the feeling of cleanliness,pureness, softness and eco-friendliness. The packaging will include 6 items, each washcloth is 10x10 inches. The details will be discussed with the designer.
Updates

Looking for a clean and neat design that will attract the buyers which will also emphasize the fact that it is made out of highest quality rayon from bamboo that don’t irritate sensitive and delicate skin. I am planning to outsource more work (website,flyers, pictures and social media related stuff) to the designers who does the best job for this packaging project .

Target Market(s)

E-commerce customers, mothers,

Colors

Designer to choose colors to be used in the design.

Requirements
Must have
• clean and stylish look that should emphasize the fact that the product is 100% organic bamboo, eco-friendly,premium ultra soft, perfect for delicate and sensitive skin and 100% natural.Kraft paper packaging might be more suitable for an eco-friendly, bamboo based product.
Nice to have
• Packaging dimensions of our first competitors is 8.3 x 5.6 x 1.4 inches and the second one is 8.2 x 5.8 x 1.5 inches therefore; the final product should be designed according to these dimensions keeping in mind that each box will have 6 towels in it.

```html
<!DOCTYPE html>
<html lang="en">
<head>
<meta charset="utf-8">
<title>Gentle Nest Co. – Bamboo Washcloths Box Layout</title>
<link rel="stylesheet" href="https://fonts.googleapis.com/css2?family=Fredoka:wght@400;600;700&family=Grandstander:wght@700&display=swap">
<style>
  :root {
    --page: #f4f1ec;
    --kraft: #c9a77c;
    --kraft-top: #bf9c70;
    --kraft-side: #b8946a;
    --kraft-edge: #a8845c;
    --window: #ececec;
    --window-shade: #dcdcdc;
    --plum: #5c2b3c;
    --plum-soft: #6e3a4c;
    --band-blue: #7fa7d8;
    --band-lilac: #a595c4;
    --band-pink: #d796b4;
    --badge-blue: #6f9fd6;
    --brand-art: #6a88bf;
    --stitch: #f3eef5;
    --bamboo: #58a33c;
    --heart: #c0303c;
    --white: #ffffff;
  }
  html, body {
    margin: 0;
    padding: 0;
    width: 1200px;
    height: 1116px;
    overflow: hidden;
    background: var(--page);
  }
  .box-layout {
    display: block;
    width: 1200px;
    height: 1116px;
  }
  .headline, .product-name {
    font-family: "Grandstander", "Fredoka", sans-serif;
    font-weight: 700;
    fill: var(--plum);
  }
  .ribbon-text {
    font-family: "Fredoka", sans-serif;
    font-weight: 700;
    fill: var(--white);
  }
  .benefits {
    font-family: "Fredoka", sans-serif;
    font-weight: 400;
    fill: var(--plum-soft);
  }
  .brand-name {
    font-family: "Fredoka", sans-serif;
    font-weight: 600;
    fill: var(--plum);
  }
  .pack-count {
    font-family: "Fredoka", sans-serif;
    font-weight: 600;
    fill: var(--white);
  }
  .pack-count-small {
    font-family: "Fredoka", sans-serif;
    font-weight: 400;
    fill: var(--white);
  }
</style>
</head>
<body>
<svg class="box-layout" viewBox="0 0 1200 1116" xmlns="http://www.w3.org/2000/svg">
  <defs>
    <linearGradient id="band-gradient" x1="0" y1="0" x2="1" y2="0">
      <stop offset="0" stop-color="var(--band-blue)"/>
      <stop offset="0.55" stop-color="var(--band-lilac)"/>
      <stop offset="1" stop-color="var(--band-pink)"/>
    </linearGradient>
    <linearGradient id="window-gradient" x1="0" y1="0" x2="0" y2="1">
      <stop offset="0" stop-color="var(--window-shade)"/>
      <stop offset="0.2" stop-color="var(--window)"/>
      <stop offset="1" stop-color="var(--window)"/>
    </linearGradient>
  </defs>

  <!-- Top panel -->
  <g class="top-panel">
    <rect x="160" y="20" width="1020" height="100" fill="var(--kraft-top)" stroke="var(--kraft-edge)" stroke-width="2"/>
    <text class="brand-name" x="670" y="77" text-anchor="middle" font-size="20">Gentle Nest Co.</text>
  </g>

  <!-- Side panel -->
  <g class="side-panel">
    <rect x="20" y="130" width="130" height="966" fill="var(--kraft-side)" stroke="var(--kraft-edge)" stroke-width="2"/>
    <text class="brand-name" transform="translate(100,170) rotate(90)" font-size="18">Gentle Nest Co.</text>
    <rect class="side-ribbon" x="100" y="470" width="40" height="420" fill="var(--plum)"/>
    <text class="ribbon-text" transform="translate(108,560) rotate(90)" font-size="20">100% Rayon from Bamboo</text>
    <text class="product-name" transform="translate(56,520) rotate(90)" font-size="46">WASHCLOTHS</text>
    <text class="benefits" transform="translate(32,460) rotate(90)" font-size="16">Ultra-Soft • Breathable • Hypoallergenic • Eco-friendly</text>
    <circle cx="85" cy="1020" r="46" fill="var(--badge-blue)"/>
    <g transform="translate(85,1020) rotate(90)">
      <text class="pack-count" x="0" y="4" text-anchor="middle" font-size="40">6</text>
      <text class="pack-count-small" x="0" y="24" text-anchor="middle" font-size="13">PER PACK</text>
    </g>
  </g>

  <!-- Front panel -->
  <rect class="front-panel" x="160" y="130" width="1020" height="966" fill="var(--kraft)" stroke="var(--kraft-edge)" stroke-width="2"/>

  <text class="headline" x="670" y="205" text-anchor="middle" font-size="42">Perfect for Sensitive &amp; Delicate Skin</text>

  <rect class="window" x="260" y="240" width="840" height="560" rx="30" fill="url(#window-gradient)"/>

  <g class="label-band">
    <rect x="160" y="790" width="1020" height="210" fill="url(#band-gradient)"/>
    <line x1="160" y1="802" x2="1180" y2="802" stroke="var(--stitch)" stroke-width="2" stroke-dasharray="8 6"/>
    <line x1="160" y1="988" x2="1180" y2="988" stroke="var(--stitch)" stroke-width="2" stroke-dasharray="8 6"/>
  </g>

  <g class="brand-badge">
    <rect x="190" y="760" width="320" height="310" rx="60" fill="var(--band-blue)" stroke="var(--stitch)" stroke-width="2" stroke-dasharray="8 6"/>
    <rect x="270" y="785" width="160" height="185" rx="20" fill="var(--brand-art)" role="img" aria-label="Illustration of a mother holding her baby"/>
    <text class="brand-name" x="350" y="1030" text-anchor="middle" font-size="28">Gentle Nest Co.</text>
  </g>

  <g class="bamboo-ribbon">
    <polygon points="540,820 1030,820 1012,846 1030,872 540,872 558,846" fill="var(--plum)"/>
    <circle cx="580" cy="846" r="32" fill="var(--white)"/>
    <rect x="566" y="814" width="28" height="64" rx="6" fill="var(--bamboo)" role="img" aria-label="Bamboo stalks icon"/>
    <text class="ribbon-text" x="625" y="857" font-size="28">100% Rayon from Bamboo</text>
  </g>

  <text class="product-name" x="560" y="940" font-size="68" letter-spacing="1">WASHCLOTHS</text>
  <text class="benefits" x="545" y="976" font-size="22">Ultra-Soft • Breathable • Hypoallergenic • Eco-friendly</text>

  <g class="pack-count-badge">
    <circle cx="1108" cy="868" r="60" fill="var(--badge-blue)"/>
    <text class="pack-count" x="1108" y="870" text-anchor="middle" font-size="54">6</text>
    <text class="pack-count-small" x="1108" y="894" text-anchor="middle" font-size="18">PER</text>
    <text class="pack-count-small" x="1108" y="914" text-anchor="middle" font-size="18">PACK</text>
  </g>

  <g class="promise">
    <path d="M570 1030 c-16 -24 -42 -16 -42 4 c0 20 24 32 42 44 c18 -12 42 -24 42 -44 c0 -20 -26 -28 -42 -4 z" fill="var(--heart)" role="img" aria-label="Heart with sleeping baby illustration"/>
    <text class="headline" x="628" y="1062" font-size="34">Made with love for little ones</text>
  </g>
</svg>
</body>
</html>
```